Vorb E-liquid (Labels for E-Liquid Company)

We are a supplier of e-cigarette supplies. We are requesting label services and design for a product we're creating. This product is an E-liquid line of Juices for electronic cigarettes. Our flavors are based off of a popular Jelly type of food. Our E-liquid line of products will have multiple flavors (up to 6) and we will need labels for each flavor. Each Label needs to satisfy our flavor description and the client buying the product needs to be able to differentiate between the flavors by seeing the "Flavor" and colors associated with that flavor on the bottle labels. Our flavor profiles are as follows.

Orange
Peach
Mango
Melon Fusion
Tropical Fusion
Strawberry

Our labels need to resemble the attached images...but we need very clear differences in the design. Label dimensions for these designs is as follows:

1.3 X 2.6 Inches

The appropriate template for these labels is attached for your size reference. Each label must represent each flavor. Each flavor profile needs to also include the necessary Nicotine Level Indication. Each flavor will be available in 0MG , 3MG , and 6MG Nicotine Levels and the label must indicate these levels BUT only one Nicotine Level to be displayed on each bottle. The label must have the "Vorb-A E-liquid". "Vorb-A" Must be in large letters and the word "E-liquid" must be below the "Vorb-A" name in smaller letters. The flavor name must be above the "Vorb-A" name preferably in the top right corner in smaller letters and the Nicotine symbol "0MG , 3MG or 6MG in small characters somewhere on the front of the label.

Our Bottles will be available in 60ml volumes. Each label must indicate this volume of measurement clearly on the front of the bottle label and only in the form "60ML"

We are here to help you with any questions you may have.

Target Market(s)

Electronic Cigarette

Industry/Entity Type

Cigarette

Requirements
Must have
• Premium E-liquid Made In the USA
Nice to have
• High quality design of course
Should not have
• low quality artwork and the design needs to look high quality, easily readable and crisp and fresh

```html
<!DOCTYPE html>
<html lang="en">
<head>
<meta charset="utf-8">
<title>Vorb-A E-liquid – Melon Fusion Label</title>
<link href="https://fonts.googleapis.com/css2?family=Montserrat:wght@200;300;700;800;900&display=swap" rel="stylesheet">
<style>
  :root {
    --page: #ffffff;
    --lime: #b3ff00;
    --lime-soft: #c6ff4a;
    --white: #ffffff;
    --brand-red: #e00000;
    --melon-red: #dc143c;
    --melon-orange: #fb8a0e;
    --melon-pale: #dcff80;
  }
  html, body {
    margin: 0;
    padding: 0;
    width: 960px;
    height: 1200px;
    overflow: hidden;
    background: var(--page);
    font-family: "Montserrat", sans-serif;
  }
  .canvas {
    position: relative;
    width: 960px;
    height: 1200px;
  }
  .label {
    position: absolute;
    left: 308px;
    top: 272px;
    width: 344px;
    height: 656px;
    border-radius: 42px;
    background: linear-gradient(180deg, var(--lime) 0%, var(--lime) 38%, var(--lime-soft) 100%);
    overflow: hidden;
    color: var(--white);
  }
  .flavor {
    position: absolute;
    right: 26px;
    top: 18px;
    margin: 0;
    text-align: right;
    font-weight: 800;
    font-size: 31px;
    line-height: 30px;
    letter-spacing: 0.5px;
  }
  .flavor-rule {
    position: absolute;
    left: 326px;
    top: 6px;
    width: 4px;
    height: 71px;
    background: var(--white);
  }
  .fruit-art {
    position: absolute;
    left: 64px;
    top: 100px;
    width: 216px;
    height: 136px;
  }
  .brand {
    position: absolute;
    left: 0;
    right: 0;
    top: 276px;
    margin: 0;
    text-align: center;
    font-weight: 900;
    font-size: 80px;
    line-height: 80px;
    color: var(--brand-red);
    letter-spacing: -1px;
  }
  .brand-sub {
    position: absolute;
    left: 0;
    right: 0;
    top: 362px;
    text-align: center;
    font-weight: 800;
    font-size: 38px;
    line-height: 40px;
    letter-spacing: 0.5px;
  }
  .volume {
    position: absolute;
    left: 0;
    right: 0;
    top: 466px;
    text-align: center;
    white-space: nowrap;
    line-height: 1;
  }
  .volume-number {
    font-weight: 200;
    font-size: 108px;
    letter-spacing: -2px;
  }
  .volume-unit {
    font-weight: 900;
    font-size: 60px;
    margin-left: 4px;
  }
  .nicotine {
    position: absolute;
    left: 0;
    right: 0;
    top: 590px;
    display: flex;
    justify-content: center;
    align-items: center;
    gap: 8px;
  }
  .nicotine-level {
    font-weight: 900;
    font-size: 38px;
    line-height: 1;
  }
  .nicotine-caption {
    font-weight: 300;
    font-size: 16px;
    line-height: 15px;
    text-transform: uppercase;
  }
</style>
</head>
<body>
<div class="canvas">
  <section class="label">
    <h2 class="flavor">MELON<br>FUSION</h2>
    <span class="flavor-rule"></span>

    <svg class="fruit-art" viewBox="0 0 216 136" role="img" aria-label="Illustration of watermelon, cantaloupe and honeydew slices">
      <defs>
        <linearGradient id="melonTones" x1="0" y1="0" x2="1" y2="0">
          <stop offset="0" stop-color="var(--melon-orange)"/>
          <stop offset="0.5" stop-color="var(--melon-red)"/>
          <stop offset="1" stop-color="var(--melon-pale)"/>
        </linearGradient>
      </defs>
      <rect x="0" y="0" width="216" height="136" rx="16" fill="url(#melonTones)" opacity="0.85"/>
    </svg>

    <h1 class="brand">Vorb-A</h1>
    <div class="brand-sub">E-LIQUID</div>

    <div class="volume">
      <span class="volume-number">60</span><span class="volume-unit">ML</span>
    </div>

    <div class="nicotine">
      <span class="nicotine-level">3MG</span>
      <span class="nicotine-caption">Nicotine<br>Level</span>
    </div>
  </section>
</div>
</body>
</html>
```